Teach English in China Website Redesign Needed

We recruit native English speakers from the US, UK, etc. who want to teach English as a foreign language in schools in China. Our target customer is college educated, age 22-28 and they love to travel. We prefer designs with bright colors and lots of photos. We want to keep all the text on our current homepage, BrightLanternPost.com. We are open to changing our logo. A competitor's page that we like is pinemeadowtutors.com because of their bright colors, photos and use of white space. We are happy to give you a dofollow link and design credit on our homepage. The use of included photos is optional. We need at least a home page design and a standard blog post design.
Target Market(s)
Our target customer is college educated, age 22-28 and they love to travel. Half of our customers are kindergarten teachers. Half of our customers are male.
Logo Text
Bright Lantern Post
Requirements
Must have
- Bright colors
Should not have
- Our homepage must not look crowded. Use white space effectively.

```html
<!DOCTYPE html>
<html lang="en">
<head>
<meta charset="utf-8">
<title>Bright Lantern Post – Teach English in China</title>
<link rel="stylesheet" href="https://fonts.googleapis.com/css2?family=Ubuntu:wght@400;500;700&family=Open+Sans:wght@400;600;700&display=swap">
<style>
:root{
  --ink:#222;
  --muted:#9a9a9a;
  --black:#0b0b0b;
  --white:#fff;
  --red:#d9534f;
  --date:#d23b3b;
  --gold:#d9a21b;
  --line:#e4e4e4;
}
*{box-sizing:border-box;margin:0;padding:0}
html,body{width:1200px;height:3377px;overflow:hidden}
body{position:relative;background:var(--white);font-family:"Open Sans",sans-serif;color:var(--ink)}
.abs{position:absolute}
.ph{position:absolute;display:block}

/* photo fills */
.photo-hero{background:
  radial-gradient(circle at 93% 40%,#fff6dc 0,#ffd08a 6%,rgba(250,150,80,.75) 18%,rgba(240,130,90,0) 42%),
  linear-gradient(90deg,rgba(50,62,84,.55) 0,rgba(50,62,84,.25) 30%,rgba(50,62,84,0) 55%),
  linear-gradient(180deg,#7fa6c6 0%,#b9c4cc 28%,#f0b483 50%,#e58e62 60%,#7d7a80 70%,#4f6275 84%,#36424f 100%)}
.photo-girl{background:
  radial-gradient(ellipse at 60% 35%,rgba(246,214,190,.9) 0,rgba(230,170,130,.6) 18%,rgba(200,110,80,0) 42%),
  radial-gradient(ellipse at 50% 95%,#f4f0ea 0,rgba(244,240,234,0) 35%),
  linear-gradient(160deg,#8a4a2c 0%,#c9794f 35%,#b8442f 65%,#8e2320 100%)}
.photo-pupils{background:
  radial-gradient(ellipse at 30% 70%,#f5f5f5 0,rgba(245,245,245,0) 35%),
  radial-gradient(ellipse at 75% 80%,#e23a2c 0,rgba(226,58,44,0) 35%),
  linear-gradient(180deg,#9bb3c7 0%,#7a8ea3 35%,#e9e9ec 65%,#c73a2e 100%)}
.photo-class{background:
  radial-gradient(ellipse at 25% 30%,#f2c230 0,rgba(242,194,48,0) 35%),
  radial-gradient(ellipse at 70% 60%,#2d3f8c 0,rgba(45,63,140,0) 40%),
  radial-gradient(ellipse at 45% 85%,#d2372c 0,rgba(210,55,44,0) 40%),
  linear-gradient(135deg,#3f6a2f,#6a5a3a 50%,#2b2f45)}
.photo-roofs{background:
  linear-gradient(180deg,rgba(150,185,215,.9) 0,rgba(150,185,215,0) 35%),
  linear-gradient(90deg,#3c5a36 0%,#6f8a5a 18%,#9ea9ae 40%,#b0b7bb 60%,#7f8f6a 78%,#a4553a 92%,#5b3a2a 100%)}
.photo-shanghai{background:
  radial-gradient(ellipse at 50% 30%,#dbe6ef 0,rgba(219,230,239,0) 55%),
  linear-gradient(180deg,#7f9cb8,#aab8c4 55%,#5d6d7d)}
.photo-shenzhen{background:
  radial-gradient(ellipse at 70% 30%,#f3c08f 0,rgba(243,192,143,0) 50%),
  linear-gradient(180deg,#6f8097,#a89c92 55%,#4d5866)}
.photo-river{background:
  radial-gradient(ellipse at 50% 18%,#e7f1f4 0,rgba(231,241,244,0) 45%),
  linear-gradient(180deg,#a9cde0 0%,#7eb3a5 32%,#3f7a5a 52%,#2d5a47 66%,#4f8c96 80%,#3a6c7a 100%)}
.photo-temple{background:
  linear-gradient(90deg,#2e4a2a 0%,#5f7a48 20%,#8a7558 38%,#7b3f2c 55%,#9a5a3a 68%,#5a7a4a 85%,#2f4a2d 100%)}
.photo-skyline{background:
  linear-gradient(180deg,#e4e7ea 0%,#cfd3d7 55%,#b7bcc2 100%)}
.photo-tower{background:linear-gradient(160deg,#8cb4dc,#3f78b5 55%,#2b5a8e)}
.photo-teacher{background:
  radial-gradient(ellipse at 55% 30%,#f0c7a6 0,rgba(240,199,166,0) 40%),
  linear-gradient(180deg,#c9ccd0 0%,#b9a496 45%,#2f3a4c 75%,#1f2836 100%)}

/* top bar */
.topbar{left:0;top:0;width:1200px;height:32px;background:var(--black);display:flex;align-items:center;padding:0 42px}
.topbar a{color:#fff;font:600 12px "Open Sans",sans-serif;text-decoration:none;margin-right:26px;letter-spacing:.3px}
.topbar .social{margin-left:auto;display:flex;gap:5px}
.topbar .social span{width:14px;height:14px;border-radius:50%;background:#777}

/* header */
.header{left:0;top:32px;width:1200px;height:126px;background:#fff}
.brand{left:45px;top:24px;width:198px;height:79px;border:3px solid var(--black);display:flex;align-items:center;justify-content:center;font:700 17px "Ubuntu",sans-serif;color:var(--black);text-align:center;line-height:1.15;padding:0 8px}
.nav{left:576px;top:50px;display:flex;gap:22px}
.nav a{font:500 16px "Ubuntu",sans-serif;color:var(--ink);text-decoration:none}
.nav a.active{border-bottom:2px solid var(--ink)}
.search{left:1124px;top:44px}

/* hero */
.hero{left:0;top:158px;width:1200px;height:553px}
.hero-small{left:42px;top:452px;font:400 30px "Ubuntu",sans-serif;color:#fff;text-shadow:0 1px 3px rgba(0,0,0,.3)}
.hero-big{left:40px;top:490px;font:500 50px "Ubuntu",sans-serif;color:#fff;letter-spacing:.5px;text-shadow:0 1px 3px rgba(0,0,0,.3)}
.arrow{width:30px;height:60px}

/* headings */
.h2{left:0;width:1200px;text-align:center;font:400 38px "Ubuntu",sans-serif;color:#333;letter-spacing:.5px}
.lead{left:320px;width:560px;text-align:center;font:400 12px/1.55 "Open Sans",sans-serif;color:#555}

/* featured blog */
.feature-text{left:518px;top:886px;width:608px;font:400 11.5px/1.55 "Open Sans",sans-serif;color:#8a8a8a}
.feature-text p{margin-bottom:10px}
.meta{font:400 11px "Open Sans",sans-serif;color:var(--date)}
.btn{display:flex;align-items:center;justify-content:center;background:var(--red);color:#fff;font:700 11px "Open Sans",sans-serif;letter-spacing:.5px;border-radius:3px;text-decoration:none}
.divider{left:0;top:1227px;width:1200px;height:2px;background:var(--line)}

/* grid */
.grid{left:115px;top:1288px;width:962px;display:grid;grid-template-columns:repeat(4,225px);column-gap:21px;row-gap:22px}
.card .thumb{width:225px;height:130px}
.card h3{font:600 12px "Open Sans",sans-serif;margin:26px 0 10px;color:#222}
.card p{font:400 9.5px/1.55 "Open Sans",sans-serif;color:#888}
.card .meta{font-size:9.5px;margin-top:12px;display:block}
.circle-btn{width:44px;height:56px;border-radius:22px;background:#cfcfcf;display:flex;align-items:center;justify-content:center}

/* city band */
.band{left:0;top:2184px;width:1200px;height:171px}
.city-card{top:7px;height:151px;width:282px;border:2px solid rgba(255,255,255,.7);display:flex;flex-direction:column;align-items:center;padding-top:40px;color:#fff;font:500 14px "Ubuntu",sans-serif;box-shadow:0 4px 10px rgba(0,0,0,.4);text-shadow:0 1px 2px rgba(0,0,0,.4)}
.city-card small{font:400 13px "Open Sans",sans-serif;margin-top:12px}

/* blog of the day */
.daily{left:0;top:2355px;width:1200px;height:471px;background:linear-gradient(180deg,#f8f8f8,#ececec)}
.daily-text{left:430px;top:2472px;width:673px;font:400 11.5px/1.55 "Open Sans",sans-serif;color:#a0a0a0}
.daily-text p{margin-bottom:10px}

/* signup band */
.signup{left:0;top:2826px;width:1200px;height:90px}
.field{top:22px;height:45px;width:135px;background:#222;border:1px solid #444}

/* apply */
.apply{left:0;top:2916px;width:1200px;height:193px}

/* footer */
.footer{left:0;top:3109px;width:1200px;height:223px;background:var(--black);color:#ddd}
.footer h4{font:600 12px "Open Sans",sans-serif;letter-spacing:1px;color:#fff;margin-bottom:16px}
.footer p,.footer li{font:400 10.5px/1.5 "Open Sans",sans-serif;color:#cfcfcf;list-style:none}
.foot-brand{left:878px;top:81px;width:191px;height:66px;background:#e6e6e6;display:flex;align-items:center;justify-content:center;font:700 17px "Ubuntu",sans-serif;color:#111;text-align:center;line-height:1.15}
.bottombar{left:0;top:3332px;width:1200px;height:45px;background:#151515;display:flex;align-items:center;padding:0 146px;font:400 10px "Open Sans",sans-serif;color:#777}
.bottombar .social{margin-left:auto;display:flex;gap:6px;margin-right:-90px}
.bottombar .social span{width:16px;height:16px;border-radius:50%;background:#888}
</style>
</head>
<body>

<nav class="abs topbar">
  <a href="#">JOB BOARD</a><a href="#">APPLY</a><a href="#">BLOG</a><a href="#">HIRE A TEACHER</a><a href="#">ABOUT US</a>
  <div class="social"><span></span><span></span><span></span><span></span><span></span><span></span></div>
</nav>

<header class="abs header">
  <div class="abs brand">Bright Lantern Post</div>
  <nav class="abs nav">
    <a class="active" href="#">Home</a><a href="#">Available Jobs</a><a href="#">Apply Online</a><a href="#">Blog</a><a href="#">About</a><a href="#">FAQ</a>
  </nav>
  <svg class="abs search" width="36" height="36" viewBox="0 0 36 36"><circle cx="15" cy="15" r="10" fill="none" stroke="#777" stroke-width="4"/><line x1="22" y1="22" x2="32" y2="32" stroke="#777" stroke-width="5" stroke-linecap="round"/></svg>
</header>

<section class="abs hero photo-hero" role="img" aria-label="Shanghai skyline across the river at sunset"></section>
<div class="abs hero-small">We will help you</div>
<div class="abs hero-big">TEACH ENGLISH IN CHINA</div>
<svg class="abs arrow" style="left:20px;top:412px" viewBox="0 0 30 60"><polyline points="22,14 8,30 22,46" fill="none" stroke="#fff" stroke-width="3"/></svg>
<svg class="abs arrow" style="left:1150px;top:412px" viewBox="0 0 30 60"><polyline points="8,14 22,30 8,46" fill="none" stroke="#fff" stroke-width="3"/></svg>

<h2 class="abs h2" style="top:752px">OUR BLOG</h2>
<p class="abs lead" style="top:806px">Lorem ipsum dolor sit amet, consectetur adipiscing elit. Nam odio magna, interdum vel neque nec, tempor sollicitudin lorem. Quisque at tincidunt odio.</p>

<div class="ph photo-girl" style="left:70px;top:883px;width:421px;height:279px" role="img" aria-label="Young girl eating noodles with chopsticks"></div>
<div class="abs feature-text">
  <p>Lorem ipsum dolor sit amet, consectetur adipiscing elit. Quisque elementum, nisl et condimentum sagittis, est felis elementum leo, vitae accumsan velit mauris sit amet odio. Maecenas id diam in elit pellentesque egestas. Integer vestibulum, ex vel scelerisque viverra, purus ligula hendrerit enim, a tristique nulla justo ac sapien. Aliquam cursus ipsum in vestibulum sapien tempor luctus. Orci varius natoque penatibus et magnis dis parturient montes, nascetur ridiculus mus.</p>
  <p>Nunc laoreet rhoncus metus, at pretium est elementum ac. Etiam consectetur enim orci, at bibendum enim ultrices quis. Sed ornare, metus vel dapibus sollicitudin, mi elit ornare sem, at vulputate ante elit id diam.</p>
  <p>In scelerisque felis eget velit posuere gravida. Sed at eleifend purus, eu finibus velit. Fusce mollis vel diam at dignissim. Nullam tristique massa et urna finibus, vitae convallis arcu luctus. Morbi finibus convallis porttitor. Duis elementum quis risus vestibulum tincidunt. Vestibulum eleifend purus non nunc mollis pulvinar. Quisque hendrerit dui vel egestas consectetur.</p>
</div>
<span class="abs meta" style="left:70px;top:1178px">09 Sep2015/By Admin/5 Comments</span>
<a class="abs btn" style="left:547px;top:1177px;width:97px;height:30px" href="#">VIEW WORK</a>
<svg class="abs" style="left:587px;top:1206px" width="18" height="8" viewBox="0 0 18 8"><polygon points="0,0 18,0 9,8" fill="var(--red)"/></svg>

<div class="abs divider"></div>

<div class="abs circle-btn" style="left:34px;top:1679px"><svg width="16" height="20" viewBox="0 0 16 20"><polyline points="12,2 4,10 12,18" fill="none" stroke="#fff" stroke-width="3"/></svg></div>
<div class="abs circle-btn" style="left:1117px;top:1679px"><svg width="16" height="20" viewBox="0 0 16 20"><polyline points="4,2 12,10 4,18" fill="none" stroke="#fff" stroke-width="3"/></svg></div>

<section class="abs grid">
  <article class="card"><div class="thumb photo-girl" role="img" aria-label="Girl eating noodles"></div><h3>Lorem ipsum dolor sit amet</h3><p>Lorem ipsum dolor sit amet, consectetur adipiscing elit, sed do eiusmod tempor incididunt ut labore et dolore magna aliqua. Ut enim ad minim veniam, quis</p><span class="meta">09 Sep2015/By Admin/5 Comments</span></article>
  <article class="card"><div class="thumb photo-pupils" role="img" aria-label="Students in uniforms lined up"></div><h3>Lorem ipsum dolor sit amet</h3><p>Lorem ipsum dolor sit amet, consectetur adipiscing elit, sed do eiusmod tempor incididunt ut labore et dolore magna aliqua. Ut enim ad minim veniam, quis</p><span class="meta">10 Sep2015/By Admin/4 Comments</span></article>
  <article class="card"><div class="thumb photo-class" role="img" aria-label="Teacher with a group of children"></div><h3>Lorem ipsum dolor sit amet</h3><p>Lorem ipsum dolor sit amet, consectetur adipiscing elit, sed do eiusmod tempor incididunt ut labore et dolore magna aliqua. Ut enim ad minim veniam, quis</p><span class="meta">10 Sep2015/By Admin/4 Comments</span></article>
  <article class="card"><div class="thumb photo-girl" role="img" aria-label="Girl eating noodles"></div><h3>Lorem ipsum dolor sit amet</h3><p>Lorem ipsum dolor sit amet, consectetur adipiscing elit, sed do eiusmod tempor incididunt ut labore et dolore magna aliqua. Ut enim ad minim veniam, quis</p><span class="meta">09 Sep2015/By Admin/5 Comments</span></article>

  <article class="card"><div class="thumb photo-girl" role="img" aria-label="Girl eating noodles"></div><h3>Lorem ipsum dolor sit amet</h3><p>Lorem ipsum dolor sit amet, consectetur adipiscing elit, sed do eiusmod tempor incididunt ut labore et dolore magna aliqua. Ut enim ad minim veniam, quis</p><span class="meta">09 Sep2015/By Admin/5 Comments</span></article>
  <article class="card"><div class="thumb photo-pupils" role="img" aria-label="Students in uniforms lined up"></div><h3>Lorem ipsum dolor sit amet</h3><p>Lorem ipsum dolor sit amet, consectetur adipiscing elit, sed do eiusmod tempor incididunt ut labore et dolore magna aliqua. Ut enim ad minim veniam, quis</p><span class="meta">10 Sep2015/By Admin/4 Comments</span></article>
  <article class="card"><div class="thumb photo-class" role="img" aria-label="Teacher with a group of children"></div><h3>Lorem ipsum dolor sit amet</h3><p>Lorem ipsum dolor sit amet, consectetur adipiscing elit, sed do eiusmod tempor incididunt ut labore et dolore magna aliqua. Ut enim ad minim veniam, quis</p><span class="meta">10 Sep2015/By Admin/4 Comments</span></article>
  <article class="card"><div class="thumb photo-girl" role="img" aria-label="Girl eating noodles"></div><h3>Lorem ipsum dolor sit amet</h3><p>Lorem ipsum dolor sit amet, consectetur adipiscing elit, sed do eiusmod tempor incididunt ut labore et dolore magna aliqua. Ut enim ad minim veniam, quis</p><span class="meta">09 Sep2015/By Admin/5 Comments</span></article>

  <article class="card"><div class="thumb photo-girl" role="img" aria-label="Girl eating noodles"></div><h3>Lorem ipsum dolor sit amet</h3><p>Lorem ipsum dolor sit amet, consectetur adipiscing elit, sed do eiusmod tempor incididunt ut labore et dolore magna aliqua. Ut enim ad minim veniam, quis</p><span class="meta">09 Sep2015/By Admin/5 Comments</span></article>
  <article class="card"><div class="thumb photo-pupils" role="img" aria-label="Students in uniforms lined up"></div><h3>Lorem ipsum dolor sit amet</h3><p>Lorem ipsum dolor sit amet, consectetur adipiscing elit, sed do eiusmod tempor incididunt ut labore et dolore magna aliqua. Ut enim ad minim veniam, quis</p><span class="meta">10 Sep2015/By Admin/4 Comments</span></article>
  <article class="card"><div class="thumb photo-class" role="img" aria-label="Teacher with a group of children"></div><h3>Lorem ipsum dolor sit amet</h3><p>Lorem ipsum dolor sit amet, consectetur adipiscing elit, sed do eiusmod tempor incididunt ut labore et dolore magna aliqua. Ut enim ad minim veniam, quis</p><span class="meta">10 Sep2015/By Admin/4 Comments</span></article>
  <article class="card"><div class="thumb photo-girl" role="img" aria-label="Girl eating noodles"></div><h3>Lorem ipsum dolor sit amet</h3><p>Lorem ipsum dolor sit amet, consectetur adipiscing elit, sed do eiusmod tempor incididunt ut labore et dolore magna aliqua. Ut enim ad minim veniam, quis</p><span class="meta">09 Sep2015/By Admin/5 Comments</span></article>
</section>

<section class="abs band photo-roofs" role="img" aria-label="Traditional Chinese rooftops and city views">
  <div class="abs city-card photo-shanghai" style="left:295px" role="img" aria-label="Shanghai waterfront">TEACH IN SHANGHAI</div>
  <div class="abs city-card photo-shenzhen" style="left:624px" role="img" aria-label="Shenzhen skyline">TEACH IN SHENZHEN<small>Apply now!</small></div>
  <svg class="abs arrow" style="left:18px;top:56px" viewBox="0 0 30 60"><polyline points="22,14 8,30 22,46" fill="none" stroke="#fff" stroke-width="3"/></svg>
  <svg class="abs arrow" style="left:1152px;top:56px" viewBox="0 0 30 60"><polyline points="8,14 22,30 8,46" fill="none" stroke="#fff" stroke-width="3"/></svg>
</section>

<section class="abs daily" role="img" aria-label="Faint city skyline backdrop"></section>
<h2 class="abs h2" style="top:2390px">BLOG OF THE DAY</h2>
<div class="ph photo-river" style="left:70px;top:2472px;width:338px;height:212px" role="img" aria-label="Fisherman on a bamboo raft on a river among karst hills"></div>
<div class="abs daily-text">
  <p>Lorem ipsum dolor sit amet, consectetur adipiscing elit. Quisque elementum, nisl et condimentum sagittis, est felis elementum leo, vitae accumsan velit mauris sit amet odio. Maecenas id diam in elit pellentesque egestas. Integer vestibulum, ex vel scelerisque viverra, purus ligula hendrerit enim, a tristique nulla justo ac sapien. Aliquam cursus ipsum in vestibulum sapien tempor luctus. Orci varius natoque penatibus et magnis dis parturient montes, nascetur ridiculus mus.</p>
  <p>Nunc laoreet rhoncus metus, at pretium est elementum ac. Etiam consectetur enim orci, at bibendum enim ultrices quis. Sed ornare, metus vel dapibus sollicitudin, mi elit ornare sem, at vulputate ante elit id diam.</p>
  <p>In scelerisque felis eget velit posuere gravida. Sed at eleifend purus, eu finibus velit. Fusce mollis vel diam at dignissim. Nullam tristique massa et urna finibus, vitae convallis arcu luctus. Morbi finibus convallis porttitor.</p>
</div>
<span class="abs meta" style="left:75px;top:2700px;color:var(--gold)">09 Sep2015/By Admin/5 Comments</span>

<section class="abs signup photo-temple" role="img" aria-label="Chinese temple rooftops among trees">
  <div class="abs field" style="left:390px"></div>
  <div class="abs field" style="left:534px"></div>
  <a class="abs btn" style="left:675px;top:22px;width:131px;height:45px" href="#">APPLY NOW</a>
</section>

<section class="abs apply photo-skyline" role="img" aria-label="Beijing skyline in soft grey">
  <div class="ph photo-tower" style="left:30px;top:10px;width:140px;height:183px" role="img" aria-label="Modern tower building"></div>
  <a class="abs btn" style="left:518px;top:72px;width:157px;height:47px;font-size:13px" href="#">APPLY NOW</a>
  <div class="ph photo-teacher" style="left:1024px;top:0;width:176px;height:193px" role="img" aria-label="Smiling male teacher"></div>
</section>

<footer class="abs footer">
  <div class="abs" style="left:146px;top:52px;width:190px">
    <h4>OUR MISSION</h4>
    <p>Lorem Ipsum is simply dummy text of the printing and typesetting industry. Lorem Ipsum has been the industry's standard dummy text ever since the 1500s, when an unknown printer took a galley of type and scrambled it to make .</p>
  </div>
  <div class="abs" style="left:378px;top:52px">
    <h4>QUICK LINKS</h4>
    <ul><li>Company</li><li>Services</li><li>Solutions</li><li>Resources</li><li>Career</li><li>Contact Us</li></ul>
  </div>
  <div class="abs" style="left:612px;top:52px;width:200px">
    <h4>CONTACT</h4>
    <div style="display:flex;gap:10px"><svg width="10" height="14" viewBox="0 0 10 14"><path d="M5 0a5 5 0 0 1 5 5c0 4-5 9-5 9S0 9 0 5a5 5 0 0 1 5-5z" fill="#ccc"/><circle cx="5" cy="5" r="2" fill="#0b0b0b"/></svg><p>742 Harbor Lane,<br>Suite 12<br>Fairview, CO 80000</p></div>
    <div style="display:flex;gap:10px;margin-top:10px"><svg width="10" height="12" viewBox="0 0 10 12"><rect x="1" y="0" width="8" height="12" rx="2" fill="#ccc"/></svg><p>+1 555 0142 880</p></div>
    <p style="margin-top:10px">0900 555 214</p>
  </div>
  <div class="abs foot-brand">Bright Lantern Post</div>
</footer>

<div class="abs bottombar">
  <span>© 2015 brightlanternpost.com All rights reserved</span>
  <div class="social"><span></span><span></span><span></span></div>
</div>

</body>
</html>
```